Residential Remodeling Contractor needs updated business card

I need a new design for my business card.
Name of the company is Ridgefell Construction. I need a card that commands presence, strength, integrity. I have been in business for 28 years. I am a Residential Remodeling Contractor that covers all aspects of a residential remodel and build.

```html
<!DOCTYPE html>
<html lang="en">
<head>
<meta charset="utf-8">
<title>Ridgefell Construction – Business Card</title>
<link rel="stylesheet" href="https://fonts.googleapis.com/css2?family=Open+Sans:wght@400;600;700&display=swap">
<style>
  :root {
    --backdrop: #232323;
    --card-blue: #213f7d;
    --card-blue-deep: #1d3873;
    --ink-white: #ffffff;
    --rule-white: rgba(255, 255, 255, 0.85);
    --emboss-blue: #3a63bd;
  }

  * { box-sizing: border-box; margin: 0; padding: 0; }

  html, body {
    width: 1200px;
    height: 780px;
    overflow: hidden;
    background: var(--backdrop);
    font-family: "Open Sans", Arial, sans-serif;
  }

  .canvas {
    position: relative;
    width: 1200px;
    height: 780px;
    display: flex;
    align-items: center;
    justify-content: center;
    gap: 40px;
  }

  .card {
    position: relative;
    width: 560px;
    height: 320px;
    background: var(--card-blue);
    color: var(--ink-white);
    overflow: hidden;
  }

  /* Front side */
  .brand {
    position: absolute;
    left: 40px;
    top: 112px;
    width: 240px;
    display: flex;
    align-items: center;
    gap: 14px;
  }

  .brand-mark {
    flex: none;
    width: 14px;
    height: 14px;
    background: var(--ink-white);
  }

  .brand-name {
    font-weight: 600;
    font-size: 26px;
    line-height: 1.15;
    letter-spacing: 0.02em;
    color: var(--ink-white);
  }

  .divider {
    position: absolute;
    left: 300px;
    top: 36px;
    width: 1px;
    height: 190px;
    background: var(--rule-white);
  }

  .person {
    position: absolute;
    left: 322px;
    top: 40px;
    right: 18px;
  }

  .person-name {
    font-weight: 700;
    font-size: 27px;
    line-height: 1.1;
  }

  .person-title {
    font-weight: 400;
    font-size: 13px;
    margin-top: 4px;
  }

  .contact-list {
    list-style: none;
    margin-top: 22px;
  }

  .contact-item {
    display: flex;
    align-items: center;
    gap: 9px;
    font-size: 13px;
    line-height: 1.75;
  }

  .contact-icon {
    width: 13px;
    height: 13px;
    flex: none;
  }

  .address {
    position: absolute;
    left: 0;
    right: 0;
    bottom: 30px;
    text-align: center;
    font-size: 13.5px;
    letter-spacing: 0.01em;
  }

  /* Back side */
  .card-back {
    background: var(--card-blue-deep);
    display: flex;
    align-items: center;
    justify-content: center;
  }

  .back-brand {
    display: flex;
    align-items: center;
    gap: 20px;
  }

  .back-mark {
    width: 22px;
    height: 22px;
    background: var(--emboss-blue);
  }

  .back-name {
    font-weight: 600;
    font-size: 40px;
    line-height: 1.1;
    letter-spacing: 0.02em;
    color: var(--emboss-blue);
  }
</style>
</head>
<body>
<main class="canvas">

  <section class="card card-front" aria-label="Business card front">
    <div class="brand">
      <span class="brand-mark" aria-hidden="true"></span>
      <p class="brand-name">Ridgefell<br>Construction</p>
    </div>

    <div class="divider" aria-hidden="true"></div>

    <div class="person">
      <h1 class="person-name">Daniel Harrow</h1>
      <p class="person-title">Managing Director</p>

      <ul class="contact-list">
        <li class="contact-item">
          <svg class="contact-icon" viewBox="0 0 16 16" aria-hidden="true">
            <path fill="#fff" d="M3.6 1.2l2.3 2.6-1.3 1.8c.9 2 2.4 3.5 4.4 4.4l1.8-1.3 2.6 2.3-1.5 2.3C6.8 14.8 1.2 9.2 1.3 3.1z"/>
          </svg>
          <span>(817) 555-0142</span>
        </li>
        <li class="contact-item">
          <svg class="contact-icon" viewBox="0 0 16 16" aria-hidden="true">
            <rect x="1" y="3" width="14" height="10" fill="#fff"/>
            <path d="M1.5 3.5L8 9l6.5-5.5" fill="none" stroke="#213f7d" stroke-width="1.4"/>
          </svg>
          <span>info@ridgefellbuild.com</span>
        </li>
        <li class="contact-item">
          <svg class="contact-icon" viewBox="0 0 16 16" aria-hidden="true">
            <circle cx="8" cy="8" r="7" fill="#fff"/>
            <path d="M1 8h14M8 1c-2.6 2.6-2.6 11.4 0 14M8 1c2.6 2.6 2.6 11.4 0 14" fill="none" stroke="#213f7d" stroke-width="1"/>
          </svg>
          <span>www.ridgefellbuild.com</span>
        </li>
      </ul>
    </div>

    <p class="address">418 Alder Bend Rd Fairhaven, Texas 75400 USA</p>
  </section>

  <section class="card card-back" aria-label="Business card back">
    <div class="back-brand">
      <span class="back-mark" aria-hidden="true"></span>
      <p class="back-name">Ridgefell<br>Construction</p>
    </div>
  </section>

</main>
</body>
</html>
```